Facebook Cover Photo & Mailchimp Template for Greyhound Racing Club

Create a consistent, professional visual identity across Facebook and email communications that promotes PWTA as a modern, community-focused greyhound racing club while respecting the heritage of greyhound racing.
Include PWTA logo.
Existing site https://www.socialpage-example.com/WestmereRunners/

```html
<!DOCTYPE html>
<html lang="en">
<head>
<meta charset="utf-8">
<title>Race Night At Westmere Greyhounds</title>
<link rel="stylesheet" href="https://fonts.googleapis.com/css2?family=Varela+Round&family=Nunito+Sans:ital,wght@1,700&display=swap">
<style>
  :root {
    --green-deep: #2f9e2a;
    --green-mid: #45b83a;
    --green-light: #6fd05e;
    --track-brown: #a07a55;
    --white: #ffffff;
  }
  * { margin: 0; padding: 0; box-sizing: border-box; }
  html, body { width: 1200px; height: 485px; overflow: hidden; background: var(--green-mid); }
  .cover {
    position: relative;
    width: 1200px;
    height: 485px;
    overflow: hidden;
    font-family: "Varela Round", Arial, sans-serif;
    color: var(--white);
  }
  .cover__backdrop {
    position: absolute;
    inset: 0;
    background: linear-gradient(160deg, var(--green-light) 0%, var(--green-mid) 45%, var(--green-deep) 100%);
  }
  .headline {
    position: absolute;
    left: 34px;
    top: 84px;
    font-size: 52px;
    line-height: 73px;
    font-weight: 400;
    letter-spacing: 0.4px;
    white-space: nowrap;
  }
  .club-name {
    position: absolute;
    left: 428px;
    top: 80px;
    font-family: "Varela Round", Arial, sans-serif;
    font-size: 46px;
    line-height: 58px;
    color: var(--white);
    letter-spacing: 2px;
  }
  .tagline {
    position: absolute;
    left: 34px;
    top: 238px;
    font-family: "Nunito Sans", Arial, sans-serif;
    font-style: italic;
    font-weight: 700;
    font-size: 30px;
    line-height: 42px;
    white-space: nowrap;
  }
  .contact {
    position: absolute;
    left: 35px;
    top: 358px;
    display: flex;
    align-items: center;
    gap: 16px;
  }
  .contact__icon { width: 56px; height: 56px; }
  .contact__label { font-size: 21px; line-height: 26px; padding-left: 3px; }
  .contact__phone { font-size: 35px; line-height: 40px; letter-spacing: 0.5px; }
  .feature-ring {
    position: absolute;
    left: 726px;
    top: 43px;
    width: 400px;
    height: 400px;
    border-radius: 50%;
    border: 2px solid rgba(255,255,255,0.85);
  }
  .feature-photo {
    position: absolute;
    left: 736px;
    top: 53px;
    width: 380px;
    height: 380px;
    border-radius: 50%;
    border: 5px solid var(--white);
    background: linear-gradient(180deg, #7f8a8e 0%, #8aa37a 35%, #d9b23a 52%, #b58c66 62%, var(--track-brown) 100%);
  }
</style>
</head>
<body>
  <main class="cover">
    <div class="cover__backdrop" role="img" aria-label="Aerial view of the greyhound racing track tinted green"></div>

    <h1 class="headline">Race Night At<br>Westmere Greyhounds</h1>
    <div class="club-name">PWTA</div>

    <p class="tagline">Where elite greyhound racing meets a<br>passionate local community.</p>

    <div class="contact">
      <svg class="contact__icon" viewBox="0 0 58 58" aria-hidden="true">
        <g fill="none" stroke="#fff" stroke-width="3" stroke-linecap="round" stroke-linejoin="round">
          <path d="M14 8 L22 8 L26 19 L20 23 C23 31 27 35 35 38 L39 32 L50 36 L50 44 C50 48 47 51 43 50 C26 47 11 32 8 15 C7 11 10 8 14 8 Z"/>
          <path d="M34 12 C41 13 45 17 46 24"/>
          <path d="M34 4 C45 5 53 13 54 24"/>
        </g>
      </svg>
      <div class="contact__text">
        <div class="contact__label">Call Us Today</div>
        <div class="contact__phone">+61 3 5550 1847</div>
      </div>
    </div>

    <div class="feature-ring" aria-hidden="true"></div>
    <div class="feature-photo" role="img" aria-label="Brindle greyhound in a blue number 4 racing rug leaping along the track rail"></div>
  </main>
</body>
</html>
```